Oakmere Animal Care Group of Central Pennsylvania

I need a business card design for a new company in Harrisburg PA called "Animal Care Oakmere Group of Central PA". I will be providing relief services for veterinarians who need coverage during vacations; sick/maternity leave, etc. I would like to see the veterinarian symbol incorporated in the design in combination with animals (dogs /cats/birds/reptiles an pocket pets). Include My full name: Tomás R. Quintaval DVM, MLAS, BS. Also include my e mail (dvmtrq@mailbrook.net) and phone number 5552846017

Target Market(s)

Small Animal Veterinarian, practice owner

Industry/Entity Type

Business

Contact Information for Business Card

Oakmere Animal Care Group of Central PA

Font styles to use
Script

Requirements
Must have
• Veterinarian caduceus (see image) and Small animals (pets) within the logo.
Nice to have
• Give a sense of relaxation (vacationing)
Should not have
• Large animals, i.e. horses, cows, zoo animals...

```html
<!DOCTYPE html>
<html lang="en">
<head>
<meta charset="utf-8">
<title>Animal Care Oakmere Group of Central PA – Business Card</title>
<link rel="stylesheet" href="https://fonts.googleapis.com/css2?family=Crimson+Text:wght@400;600&family=Great+Vibes&display=swap">
<style>
  :root {
    --page-bg: #e8e5e0;
    --card-white: #fbfbfb;
    --brand-blue: #2aa3d6;
    --brand-blue-deep: #1d8fc4;
    --navy: #3a4b62;
    --navy-light: #566a85;
    --ink-grey: #4a4f57;
    --icon-grey: #6c7078;
  }
  * { margin: 0; padding: 0; box-sizing: border-box; }
  html, body {
    width: 1200px;
    height: 818px;
    overflow: hidden;
    background: var(--page-bg);
  }
  .canvas {
    position: relative;
    width: 1200px;
    height: 818px;
  }
  .card {
    position: absolute;
    left: 100px;
    top: 123px;
    width: 1000px;
    height: 572px;
    background: var(--card-white);
    overflow: hidden;
    box-shadow: 0 10px 30px rgba(0,0,0,0.18);
  }
  .card-art {
    position: absolute;
    inset: 0;
  }
  .logo-ring {
    position: absolute;
    left: 62px;
    top: 168px;
    width: 168px;
    height: 168px;
    border-radius: 50%;
    border: 9px solid var(--navy);
  }
  .company {
    position: absolute;
    left: 252px;
    top: 190px;
    font-family: "Crimson Text", serif;
    font-variant: small-caps;
    line-height: 1;
  }
  .company-name {
    display: block;
    color: var(--brand-blue);
    font-size: 46px;
    font-weight: 600;
    letter-spacing: 1px;
  }
  .company-region {
    display: block;
    margin-top: 6px;
    color: var(--ink-grey);
    font-size: 36px;
    font-weight: 400;
    letter-spacing: 1px;
  }
  .person {
    position: absolute;
    left: 262px;
    top: 330px;
  }
  .person-name {
    display: block;
    font-family: "Great Vibes", cursive;
    color: var(--brand-blue);
    font-size: 50px;
    line-height: 1;
    word-spacing: 10px;
    white-space: nowrap;
  }
  .person-role {
    display: block;
    margin-top: 4px;
    font-family: "Crimson Text", serif;
    color: var(--ink-grey);
    font-size: 27px;
  }
  .contact {
    position: absolute;
    left: 480px;
    top: 48px;
    list-style: none;
    font-family: "Crimson Text", serif;
    color: var(--ink-grey);
    font-size: 26px;
  }
  .contact-item {
    display: flex;
    align-items: center;
    gap: 14px;
    height: 40px;
    white-space: nowrap;
  }
  .contact-icon {
    width: 26px;
    height: 26px;
    flex: none;
  }
</style>
</head>
<body>
<main class="canvas">
  <section class="card" aria-label="Business card front">
    <svg class="card-art" width="1000" height="572" viewBox="0 0 1000 572">
      <defs>
        <linearGradient id="pet-silhouette-tone" x1="0" y1="0" x2="1" y2="1">
          <stop offset="0" stop-color="#35b6e3"/>
          <stop offset="1" stop-color="#1f8fc3"/>
        </linearGradient>
      </defs>
      <line x1="240" y1="160" x2="790" y2="160" stroke="var(--brand-blue)" stroke-width="2.5"/>
      <line x1="252" y1="318" x2="720" y2="318" stroke="var(--brand-blue)" stroke-width="2.5"/>
      <line x1="252" y1="440" x2="760" y2="440" stroke="var(--brand-blue)" stroke-width="2.5"/>
      <path role="img" aria-label="Large blue pet silhouette illustration"
            d="M820 0 L1000 0 L1000 420 L855 420 C835 360 830 300 800 250 C780 210 760 170 790 120 C810 80 815 40 820 0 Z"
            fill="url(#pet-silhouette-tone)"/>
      <polygon points="0,478 800,478 840,430 1000,430 1000,442 846,442 806,490 0,490" fill="var(--brand-blue)"/>
      <polygon points="0,500 815,500 855,452 1000,452 1000,572 0,572" fill="var(--navy)"/>
      <polygon points="0,540 1000,540 1000,548 0,548" fill="var(--navy-light)"/>
    </svg>

    <div class="logo-ring" aria-hidden="true"></div>

    <h1 class="company">
      <span class="company-name">Animal Care Oakmere</span>
      <span class="company-region">Group of Central PA</span>
    </h1>

    <p class="person">
      <span class="person-name">Tomás R. Quintaval</span>
      <span class="person-role">Managing Director</span>
    </p>

    <ul class="contact">
      <li class="contact-item">
        <svg class="contact-icon" viewBox="0 0 26 26" aria-label="Phone">
          <rect x="1" y="1" width="24" height="24" rx="3" fill="var(--icon-grey)"/>
          <path d="M8 7 L11 7 L12 10 L10.5 11.5 C11.5 13.5 12.5 14.5 14.5 15.5 L16 14 L19 15 L19 18 C14 19 7 12 8 7 Z" fill="#fff"/>
        </svg>
        <span>5552846017</span>
      </li>
      <li class="contact-item">
        <svg class="contact-icon" viewBox="0 0 26 26" aria-label="Email">
          <rect x="1" y="1" width="24" height="24" rx="3" fill="var(--icon-grey)"/>
          <rect x="5" y="8" width="16" height="11" fill="none" stroke="#fff" stroke-width="1.6"/>
          <polyline points="5,8 13,14 21,8" fill="none" stroke="#fff" stroke-width="1.6"/>
        </svg>
        <span>dvmtrq@mailbrook.net</span>
      </li>
    </ul>
  </section>
</main>
</body>
</html>
```